Cruise Booking Website

Cruise search and booking website

This project is a redesign of a cruise booking website we did a few years ago.

The current website is located here: http://voyage.pylonworks.example/en/

It's not fully functional but gives you ad idea how miserable the old design was.

All the information about cruises, cruise lines, destinations, ports and shore excursions will be similar to http://www.sailquest.example/
Actual search pages (form, results, single result, sailing and cabin selection, ship info, booking) will have EXACTLY the same info as sailquest.example

We like the style of http://harborfleetdesk.example, it's quite modern, good spacing, not overloaded with information. So you can use it as an example of what we like, not what we want as a final result for us. Please, don't copy it. The result should not be possible to resemble the harborfleetdesk.example, because our site has to be unique. This is important!
If you submit a design that clearly reminds another cruise site it will be rejected!

Also the mockup provided is just to give you the basic structure and show what information has to be present on the page. It doesn't mean the layout has to be the same as a mockup. The layout is up to the designer.

I've updated the mockup to be more generic so it doesn't confuse you:
https://files.boxvault.example/s/k7m2qp9wz4hx/Home%20page.png

When you're adding social sharing icons like plazanet/chirpline you have to use chinese ones instead:
https://files.boxvault.example/s/t3nr8vx5lc2e/chinese-social-icons.png
Originals: http://minilk.example/qR7t

We'll start with home page first and after it's approved inner pages can be designed.

I know the cost of the project doesn't look high, but the task is straight forward and doesn't require to be very original, it's better to follow existing design and layout patterns that proved to work well.
That's why I encourage you to choose a template to build the design on top of one of https://themeparlor.example/ themes if it will save the design work, will be easier and faster for you. So it will be more like a customization than a new design from scratch.

Mockups, site map and logo files:
- https://files.boxvault.example/sh/h48dm2rs73fkpw/QvnbW2Xz8e

Website tree:
- https://sheets.papernest.example/document/d/7xPqR2mLw9sTk4VbN8cHj3YzA6eUf5GdKo1iMnBv/edit?usp=sharing
Updates

So far a lot of designs are just copying http://www.harborfleetdesk.example/ - we don't like it!

We like the style of harborfleetdesk.example, it's quite modern, good spacing, not overloaded with information. So you can use it as an example of what we like, not what we want as a final result for us. Please, don't copy it. The result should not be possible to resemble the harborfleetdesk.example, because our site has to be unique. This is important!

Target Market(s)

Chinese travellers

Industry/Entity Type

Build

Requirements
Must have
• * White, blue and red
* Large spacing, not too much information cramped into a small space like sailquest.example or the current website
* More "hidden" info in popups, tabs and so on, so not to many things are visible at the same time
* Compatible with kestrel scaffold styling (for easier coding):
- http://kestrelkit.codeshelf.example/scaffold/index.html
- http://skinmarket.example/
* Feel free to propose to build the design on top of one of https://themeparlor.example/ themes if it will save the design work, will be easier and faster for you

```html
<!DOCTYPE html>
<html lang="en">
<head>
<meta charset="utf-8">
<title>Haiyun Voyages – Home</title>
<link href="https://fonts.googleapis.com/css2?family=Ubuntu:wght@400;500;700&display=swap" rel="stylesheet">
<style>
:root{
  --bg-deep:#2467a3;
  --bg-light:#b9d6ee;
  --white:#ffffff;
  --blue:#1a80c8;
  --blue-dark:#0c5c9e;
  --navy:#0d3f6e;
  --nav-top:#2b9ae0;
  --nav-bottom:#0a6cb5;
  --panel:#2a7fc1;
  --panel-dark:#1d6aa9;
  --orange:#f7941d;
  --orange-light:#fbb040;
  --text:#555c63;
  --muted:#8a9096;
  --line:#e3e6ea;
  --footer:#3c76ab;
  --footer-dark:#336a9c;
}
*{box-sizing:border-box;margin:0;padding:0}
html,body{width:1006px;height:1200px;overflow:hidden}
body{font-family:"Ubuntu",sans-serif;color:var(--text);
  background:radial-gradient(ellipse 70% 60% at 50% 45%,var(--bg-light) 0%,#6fa6d4 45%,var(--bg-deep) 100%);position:relative}
.abs{position:absolute}
.page{position:absolute;left:150px;top:0;width:705px;height:1200px;background:var(--white)}
.photo{position:absolute;display:block}
/* header */
.logo{left:13px;top:32px;display:flex;align-items:center;gap:7px}
.logo-dot{width:34px;height:34px;border-radius:50%;background:var(--blue)}
.logo-name{font-size:24px;font-weight:700;color:var(--blue-dark);letter-spacing:-.3px;line-height:1}
.logo-url{position:absolute;left:41px;top:29px;font-size:8px;font-weight:700;color:var(--blue-dark);white-space:nowrap}
.account{left:515px;top:14px;font-size:9px;color:var(--blue)}
.account span{margin:0 6px;color:var(--muted)}
.socials{left:607px;top:10px;display:flex;gap:4px}
.socials i{width:18px;height:18px;border-radius:4px;display:block}
.call{left:382px;top:43px}
.call-num{position:absolute;left:32px;top:-2px;font-size:16px;font-weight:700;color:var(--blue);white-space:nowrap}
.call-txt{position:absolute;left:32px;top:16px;font-size:12px;color:#333;white-space:nowrap}
.search{left:525px;top:55px;width:166px;height:19px;border:1px solid #cfd3d7;border-radius:3px;font-size:7px;color:#888;padding:5px 8px}
/* nav */
.nav{left:0;top:94px;width:705px;height:28px;background:linear-gradient(var(--nav-top),var(--nav-bottom));display:flex}
.nav a{color:#fff;font-size:8.5px;font-weight:700;text-decoration:none;line-height:28px;text-align:center;border-right:1px solid rgba(0,0,0,.18)}
.nav a.active{background:linear-gradient(#3aa9ec,#1a8ad4)}
/* finder */
.finder{left:16px;top:138px;width:208px;height:293px;background:var(--panel);border:2px solid #4a9ad6;border-radius:3px;color:#e2eefa}
.finder h2{font-size:17px;font-weight:400;color:#fff;padding:15px 0 8px 18px;border-bottom:1px solid rgba(255,255,255,.15)}
.lbl{position:absolute;font-size:9px;color:#dbe9f6;line-height:11px}
.lbl.big{font-size:11px;color:#fff;line-height:13px}
.sel{position:absolute;height:19px;background:linear-gradient(#f4f4f4,#dcdcdc);border-radius:2px;font-size:7.5px;color:#333;padding:5px 8px}
.sel::after{content:"";position:absolute;right:0;top:0;width:17px;height:19px;border-left:1px solid #c6c6c6}
.senior{position:absolute;left:17px;top:232px;font-size:7.5px;color:#dbe9f6;display:flex;gap:3px;align-items:center}
.senior i{width:9px;height:9px;background:#e5eef7;border-radius:1px}
.btn-search{position:absolute;left:16px;top:249px;width:176px;height:28px;background:linear-gradient(var(--orange-light),var(--orange));border:1px solid #f08a10;border-radius:3px;color:#fff;font-size:12px;font-weight:500;text-align:center;line-height:26px}
/* newsletter */
.news{left:16px;top:450px;width:208px;height:249px;background:linear-gradient(var(--panel),var(--panel-dark));border:2px solid #4a9ad6;border-radius:3px;color:#fff}
.news .frame{position:absolute;left:9px;top:9px;width:188px;height:113px;background:#fff;padding:4px}
.news h3{position:absolute;left:16px;top:133px;font-size:11px;font-weight:500}
.news p{position:absolute;left:16px;top:152px;font-size:7px}
.news .email{position:absolute;left:16px;top:170px;width:180px;height:18px;background:#fff;border-radius:2px;font-size:7px;color:#888;padding:5px 39px}
.news .sub{position:absolute;left:17px;top:197px;width:74px;height:18px;background:var(--navy);font-size:8px;text-align:center;line-height:18px}
.news .rules{position:absolute;left:19px;top:225px;font-size:8.5px}
/* main */
.crumbs{left:248px;top:139px;font-size:7.5px;color:var(--blue-dark)}
.slider{left:244px;top:162px;width:445px;height:227px;overflow:hidden}
.caption{position:absolute;left:0;bottom:0;width:100%;height:44px;background:rgba(20,20,20,.82);color:#fff}
.caption h1{position:absolute;left:12px;top:6px;font-size:17px;font-weight:700}
.caption p{position:absolute;left:14px;top:28px;font-size:7.5px}
.dots{position:absolute;right:12px;top:18px;display:flex;gap:3px}
.dots i{width:8px;height:8px;border-radius:50%;background:#888}
.dots i:first-child{background:#ddd}
.tabs{left:244px;top:415px;height:26px;display:flex;gap:2px}
.tabs span{height:26px;background:linear-gradient(#fba53a,var(--orange));color:#fff;font-size:7px;font-weight:500;text-align:center;line-height:26px}
.tabs span.on{background:linear-gradient(#1a6db0,var(--navy))}
.hl{left:244px;top:441px;width:445px;height:262px;border:1px solid var(--line);border-top:2px solid var(--orange)}
.hl h2{position:absolute;left:21px;top:12px;font-size:12.5px;font-weight:500;color:var(--blue-dark)}
.item{position:absolute;width:195px;height:62px}
.item .photo{left:0;top:0;width:64px;height:55px}
.item h4{position:absolute;left:76px;top:1px;font-size:8px;font-weight:400;color:var(--orange)}
.item p{position:absolute;left:78px;top:15px;width:118px;font-size:6.5px;line-height:13px;color:var(--muted)}
.item.sep::after{content:"";position:absolute;left:0;bottom:-8px;width:195px;border-top:1px solid var(--line)}
/* deals */
.deals{left:14px;top:722px;width:680px;height:180px;background:linear-gradient(#fff 0%,#e8edf1 100%);border:1px solid #d7dde3}
.deals-bar{position:absolute;left:0;top:0;width:100%;height:25px;background:linear-gradient(#2b9ae0,#0d72bb);color:#fff;font-size:7.5px;line-height:25px;padding:0 15px}
.deals-bar a{position:absolute;right:12px;color:#fff;text-decoration:underline}
.card{position:absolute;top:38px;width:148px;height:125px;background:#fff;border:1px solid #e0e3e6}
.card .photo{left:3px;top:3px;width:140px;height:78px}
.card h5{position:absolute;left:5px;top:91px;font-size:7.5px;font-weight:400;color:var(--navy)}
.card b{position:absolute;left:5px;top:107px;font-size:8.5px;font-weight:400;color:var(--orange)}
.arrow{position:absolute;width:24px;height:24px;border-radius:50%;background:var(--orange)}
.partners-title{left:14px;top:909px;font-size:12.5px;font-weight:500;color:var(--blue-dark)}
.pager{left:660px;top:909px;display:flex;gap:2px}
.pager i{width:15px;height:15px;background:#d4d7da;display:block}
.partner{position:absolute;top:934px;width:104px;height:53px;border:1px solid #dcdfe2;background:#fff}
.partner i{position:absolute;left:28px;top:17px;width:48px;height:18px;border-radius:9px}
/* footer */
.footer{left:0;top:1005px;width:705px;height:195px;background:var(--footer);color:#fff}
.footer h4{position:absolute;font-size:11px;font-weight:500}
.footer ul{position:absolute;list-style:none;font-size:7px;line-height:16px}
.f-logo{position:absolute;left:292px;top:53px;width:71px;height:70px;background:#fff;display:flex;flex-direction:column;align-items:center;justify-content:center;gap:5px}
.f-logo i{width:28px;height:28px;border-radius:50%;background:var(--blue)}
.f-logo span{font-size:6.5px;font-weight:700;color:var(--blue-dark)}
.f-about{position:absolute;left:377px;top:61px;width:100px;font-size:8px;line-height:13px}
.f-contact{position:absolute;left:508px;top:52px;font-size:8.5px;line-height:14px}
.f-line{position:absolute;left:508px;font-size:8px;display:flex;gap:6px;align-items:center}
.copyright{position:absolute;left:0;bottom:0;width:100%;height:36px;background:var(--footer-dark);font-size:6.5px;text-align:center;line-height:44px}
</style>
</head>
<body>
<div class="page">
  <header>
    <div class="abs logo"><i class="logo-dot"></i><span class="logo-name">Haiyun Voyages</span><span class="logo-url">www.haiyunvoyages.example</span></div>
    <div class="abs account">Sign in<span>|</span>Signup</div>
    <div class="abs socials"><i style="background:#e5362c"></i><i style="background:#26a8df"></i><i style="background:#f5a01a"></i><i style="background:#d9302d"></i></div>
    <div class="abs call">
      <svg width="27" height="27" viewBox="0 0 27 27"><circle cx="13.5" cy="13.5" r="12" fill="none" stroke="#8e959c" stroke-width="1.6"/><path d="M9.5 7.5c-1.5 1-2 3 -.8 5.8c1.4 3.2 3.6 5.6 6 6.6c1.4.6 2.6.2 3.4-.8l-2.4-2.4l-1.6 1c-1.4-.6-3-2.4-3.8-4.2l1.4-1.2z" fill="#6d747b"/></svg>
      <span class="call-num">400 318 529</span><span class="call-txt">Call Us Today!</span>
    </div>
    <div class="abs search">SEARCH :
      <svg class="abs" style="right:6px;top:4px" width="10" height="10" viewBox="0 0 10 10"><circle cx="4" cy="4" r="3" fill="none" stroke="#bbb" stroke-width="1.2"/><path d="M6.2 6.2L9 9" stroke="#bbb" stroke-width="1.2"/></svg>
    </div>
  </header>
  <nav class="abs nav">
    <a class="active" style="width:74px">HOME</a><a style="width:100px">DESTINATIONS</a><a style="width:93px">CRUISE LINES</a><a style="width:91px">CRUISE INFO</a><a style="width:86px">DEALS</a><a style="width:110px">ONLINE BOOKING</a><a style="width:89px">CONTACT US</a><a style="width:62px;border-right:0">BLOG</a>
  </nav>

  <aside class="abs finder">
    <h2>Find Your Cruise</h2>
    <span class="lbl" style="left:18px;top:56px">Destination</span>
    <div class="sel" style="left:18px;top:69px;width:172px">Destination name</div>
    <span class="lbl" style="left:18px;top:94px">Length</span><span class="lbl" style="left:111px;top:94px">Month</span>
    <div class="sel" style="left:18px;top:107px;width:79px">Length Area</div>
    <div class="sel" style="left:111px;top:107px;width:79px"></div>
    <span class="lbl" style="left:17px;top:134px">Cruise Lines</span>
    <div class="sel" style="left:16px;top:147px;width:174px">Any Cruise line</div>
    <span class="lbl big" style="left:17px;top:176px">Number of Travelers</span>
    <span class="lbl" style="left:18px;top:194px">Age 25+</span><span class="lbl" style="left:111px;top:194px">Age 0 to 24</span>
    <div class="sel" style="left:18px;top:207px;width:78px">5</div>
    <div class="sel" style="left:111px;top:207px;width:78px">0</div>
    <div class="senior" style="top:234px"><i></i>Check for senior rates</div>
    <div class="btn-search">Search Cruises</div>
  </aside>

  <aside class="abs news">
    <div class="frame"><div class="photo" role="img" aria-label="Senior couple relaxing in deck chairs by a pool" style="position:static;width:180px;height:105px;background:linear-gradient(170deg,#3aa8d8 0%,#7fcbe6 35%,#e8f2f6 55%,#f1d6b4 75%,#cf9c6a 100%)"></div></div>
    <h3>Cruise Deals Newsletter</h3>
    <p>Subscribe to the best Cruise deals Now!</p>
    <div class="email">Email :</div>
    <div class="sub">Subscribe</div>
    <div class="rules">Contest Rules</div>
  </aside>

  <div class="abs crumbs">HOME &nbsp;›&nbsp; BREADCRUMBS</div>
  <section class="abs slider">
    <div class="photo" role="img" aria-label="Group of friends walking together along a sunny beach" style="left:0;top:0;width:445px;height:227px;background:linear-gradient(180deg,#c4d9e8 0%,#e6edf0 22%,#d9dcd6 38%,#b9c4c2 55%,#8fa0a4 75%,#c7c2b2 100%)"></div>
    <div class="caption"><h1>CORALLINE CRUISES</h1><p>YOUR SAILING PARTNER AROUND THE WORLD</p><div class="dots"><i></i><i></i><i></i><i></i><i></i></div></div>
  </section>

  <div class="abs tabs"><span style="width:104px">OVERVIEW</span><span style="width:96px">SHIPS</span><span class="on" style="width:96px">HIGHLIGHTS</span><span style="width:110px">FEATURED CRUISES</span></div>
  <section class="abs hl">
    <h2>CORALLINE CRUISE LINE HIGHLIGHTS</h2>
    <div class="item sep" style="left:18px;top:36px"><div class="photo" role="img" aria-label="Child on a rope swing at sea" style="background:linear-gradient(#b8c9d8,#7fa6c8 40%,#49698b 75%,#3a4a5a)"></div><h4>CHILDREN'S ACTIVITIES</h4><p>Kids love Camp Coralline. It's fun and offers a wide range of activities for kids aged 2-11. The activities...</p></div>
    <div class="item sep" style="left:233px;top:36px"><div class="photo" role="img" aria-label="Starfish on sand" style="background:linear-gradient(#4aa6dc,#9fd0ea 35%,#e2c79a 55%,#d9a25a)"></div><h4>CHILDREN'S ACTIVITIES</h4><p>Kids love Camp Coralline. It's fun and offers a wide range of activities for kids aged 2-11. The activities...</p></div>
    <div class="item sep" style="left:18px;top:114px"><div class="photo" role="img" aria-label="Beach chairs facing the sea" style="background:linear-gradient(#6fb8e6,#2f8fd0 40%,#3fa3d6 60%,#d8c7a5)"></div><h4>CHILDREN'S ACTIVITIES</h4><p>Kids love Camp Coralline. It's fun and offers a wide range of activities for kids aged 2-11. The activities...</p></div>
    <div class="item sep" style="left:233px;top:114px"><div class="photo" role="img" aria-label="Long-tail boats on turquoise water" style="background:linear-gradient(#9dbccc,#4a8a8c 45%,#2f7a78 65%,#6b5a40)"></div><h4>CHILDREN'S ACTIVITIES</h4><p>Kids love Camp Coralline. It's fun and offers a wide range of activities for kids aged 2-11. The activities...</p></div>
    <div class="item" style="left:18px;top:191px"><div class="photo" role="img" aria-label="Camel resting in the desert" style="background:linear-gradient(#2f6fb8,#5d90c8 35%,#c99a55 60%,#a26e30)"></div><h4>CHILDREN'S ACTIVITIES</h4><p>Kids love Camp Coralline. It's fun and offers a wide range of activities for kids aged 2-11. The activities...</p></div>
    <div class="item" style="left:233px;top:191px"><div class="photo" role="img" aria-label="Friends reading a book together" style="background:linear-gradient(#7a3a2a,#c98a6a 45%,#a86048 70%,#5a3a30)"></div><h4>CHILDREN'S ACTIVITIES</h4><p>Kids love Camp Coralline. It's fun and offers a wide range of activities for kids aged 2-11. The activities...</p></div>
  </section>

  <section class="abs deals">
    <div class="deals-bar">LAST MINUTE DEALS :<a>View all last minute deals</a></div>
    <div class="arrow" style="left:2px;top:69px"><svg width="24" height="24" viewBox="0 0 24 24"><path d="M14 8l-4 4l4 4" fill="none" stroke="#fff" stroke-width="1.8"/></svg></div>
    <div class="card" style="left:18px"><div class="photo" role="img" aria-label="Family running on a beach" style="background:linear-gradient(#2f8fd8,#7fc0ea 45%,#cfe6f2 62%,#e6dccb 80%,#d8c8ae)"></div><h5>3 day cruise to the Bahamas</h5><b>¥ 9000</b></div>
    <div class="card" style="left:184px"><div class="photo" role="img" aria-label="Rocky island in clear turquoise sea" style="background:linear-gradient(#1f5fa8,#3a7ab8 25%,#a88a5a 45%,#2aa6c8 65%,#1883b0)"></div><h5>3 day cruise to the Bahamas</h5><b>¥ 9000</b></div>
    <div class="card" style="left:349px"><div class="photo" role="img" aria-label="City beach with hotels and mountains" style="background:linear-gradient(#4a86b8,#5f8a78 35%,#cfd6d2 50%,#3fa8a8 70%,#d9d0b8)"></div><h5>3 day cruise to the Bahamas</h5><b>¥ 9000</b></div>
    <div class="card" style="left:514px"><div class="photo" role="img" aria-label="Couple taking a photo together" style="background:linear-gradient(#c88a5a,#9a5a38 45%,#6a3a28 70%,#3a2a22)"></div><h5>3 day cruise to the Bahamas</h5><b>¥ 9000</b></div>
    <div class="arrow" style="left:658px;top:69px"><svg width="24" height="24" viewBox="0 0 24 24"><path d="M10 8l4 4l-4 4" fill="none" stroke="#fff" stroke-width="1.8"/></svg></div>
  </section>

  <h2 class="abs partners-title">OUR RELIABLE PARTNERS</h2>
  <div class="abs pager"><i></i><i></i></div>
  <div class="partner" style="left:15px"><i style="background:#c8342c"></i></div>
  <div class="partner" style="left:130px"><i style="background:#1d4f9c"></i></div>
  <div class="partner" style="left:245px"><i style="background:#2a4a6c"></i></div>
  <div class="partner" style="left:360px"><i style="background:#f59a3a"></i></div>
  <div class="partner" style="left:474px"><i style="background:#4aa3d8"></i></div>
  <div class="partner" style="left:589px"><i style="background:#1e6fb8"></i></div>

  <footer class="abs footer">
    <h4 style="left:24px;top:27px">Useful Pages</h4>
    <ul style="left:24px;top:46px"><li>About Us</li><li>Contact us</li><li>Blog</li><li>FAQ</li><li>Terms of Service</li><li>Payment info</li><li>Reward Points</li></ul>
    <h4 style="left:160px;top:27px">Cruise Infov</h4>
    <ul style="left:161px;top:46px"><li>Cruise news</li><li>Visa</li><li>Honeymoon cruises</li><li>Firsttime on a Cruise</li></ul>
    <h4 style="left:292px;top:32px">About haiyunvoyages.example</h4>
    <div class="f-logo"><i></i><span>Haiyun Voyages</span></div>
    <p class="f-about">We're the most advanced cruise booking providr in china.</p>
    <h4 style="left:508px;top:32px">Contact Us</h4>
    <p class="f-contact">Brightkeel Studio Pte Ltd<br>Larkfield Centre x118, Harbour Ave 3.2<br>Tidewater 20871 Indonesia</p>
    <div class="f-line" style="top:100px"><svg width="11" height="9" viewBox="0 0 11 9"><path d="M1 3c2-2.4 7-2.4 9 0l-1.6 1.2l-1.4-1.2h-3l-1.4 1.2z M2.5 5h6l1 3.5h-8z" fill="#fff"/></svg>(021) 555-0143 - (021) 555-0178</div>
    <div class="f-line" style="top:118px"><svg width="11" height="9" viewBox="0 0 11 9"><rect x=".5" y=".5" width="10" height="8" fill="none" stroke="#fff"/><path d="M.5 .5l5 4.5l5-4.5" fill="none" stroke="#fff"/></svg>hello@haiyunvoyages.example</div>
    <div class="copyright">© 2013. haiyunvoyages. All rights reserved.</div>
  </footer>
</div>
</body>
</html>
```